need corporate, modern business card created for Consulting Company

I need a slick business card using elements from my website, as well as, integrating my pixelforge-created logo (see files).

The business card needs to be:
1. Corporate and modern
2. Clean and professional

I've included a PSD with the logo/icon that you can use to create it. Feel free to try a metallic finish on the logo, make it bigger/small, underlay it. Whatever you need to do to make my card stand out.

Try a black background, or white background or gray.

The idea is for my card to be memorable as well as professional and corporate.

Target Market(s)

Corporate business in the US and Canada.

Industry/Entity Type

Business

Contact Information for Business Card

Commerce Advancing Methods
Martin Coles, Senior Partner
office: 1 877 555 0143
mobile: 1 519 555 0172
website: http://www.brightvale.example

Requirements
Must have
• Card-related information
• corporate, yet modern
• clean and professional
• incorporate the icon only
• must have an editable form when complete!
Nice to have
• metallic icon might be cool
• try it with white or black

```html
<!DOCTYPE html>
<html lang="en">
<head>
<meta charset="utf-8">
<title>Brightvale Business Card</title>
<link rel="stylesheet" href="https://fonts.googleapis.com/css2?family=Questrial&family=Open+Sans:wght@400;700&display=swap">
<style>
  :root {
    --bg: #e9e7e3;
    --card: #ffffff;
    --ink: #262626;
    --ink-soft: #3a3a3a;
    --blue: #3f8fd6;
    --blue-light: #5aaee0;
    --rule: #2f2f2f;
  }
  * { box-sizing: border-box; margin: 0; padding: 0; }
  html, body { width: 1200px; height: 886px; overflow: hidden; }
  body {
    background: var(--bg);
    display: flex;
    justify-content: center;
    align-items: center;
    gap: 90px;
    font-family: "Open Sans", Arial, sans-serif;
    color: var(--ink);
  }
  .card {
    position: relative;
    width: 420px;
    height: 735px;
    background: var(--card);
    box-shadow: 0 4px 18px rgba(0,0,0,0.12);
    overflow: hidden;
  }
  .tab {
    position: absolute;
    background: var(--blue);
  }

  /* Contact side */
  .card--contact .tab--top { top: 0; left: 150px; width: 120px; height: 48px; }
  .card--contact .tab--bottom { bottom: 0; left: 150px; width: 120px; height: 48px; }
  .wordmark {
    font-family: "Questrial", "Century Gothic", sans-serif;
    color: var(--ink);
    letter-spacing: 1px;
  }
  .card--contact .wordmark {
    position: absolute;
    top: 78px;
    width: 100%;
    text-align: center;
    font-size: 46px;
  }
  .icon-panel {
    position: absolute;
    top: 170px;
    left: 105px;
    width: 210px;
    height: 140px;
    background: linear-gradient(135deg, var(--blue), var(--blue-light));
  }
  .contact-list {
    position: absolute;
    top: 360px;
    left: 60px;
    width: 300px;
    list-style: none;
    text-align: center;
    font-size: 16px;
    color: var(--ink-soft);
  }
  .contact-list li {
    padding: 9px 0 7px;
    border-bottom: 1px solid var(--rule);
  }
  .address {
    position: absolute;
    top: 565px;
    left: 40px;
    width: 340px;
    text-align: center;
    font-size: 16px;
    line-height: 1.35;
    color: var(--ink-soft);
    font-style: normal;
  }

  /* Name side */
  .card--name .tab--corner { top: 0; left: 40px; width: 110px; height: 46px; }
  .brand {
    position: absolute;
    top: 250px;
    left: 0;
    width: 100%;
    text-align: center;
  }
  .brand__mark {
    display: inline-flex;
    align-items: center;
    gap: 12px;
  }
  .brand__square {
    width: 30px;
    height: 30px;
    background: var(--blue);
  }
  .card--name .wordmark { font-size: 50px; }
  .tagline {
    margin-top: 2px;
    font-family: "Questrial", "Century Gothic", sans-serif;
    font-size: 17px;
    color: var(--ink-soft);
    letter-spacing: 0.5px;
  }
  .person {
    position: absolute;
    right: 40px;
    bottom: 95px;
    text-align: right;
  }
  .person__name { font-size: 34px; font-weight: 700; color: var(--ink); }
  .person__title { font-size: 14px; color: var(--ink-soft); margin-top: -2px; }
</style>
</head>
<body>

  <section class="card card--contact">
    <div class="tab tab--top"></div>
    <div class="wordmark">brightvale</div>
    <div class="icon-panel" role="img" aria-label="Brand icon on blue panel"></div>
    <ul class="contact-list">
      <li>office: 1 877 555 0143</li>
      <li>mobile: 1 519 555 0172</li>
      <li>www.brightvale.example</li>
      <li>info@brightvale.example</li>
    </ul>
    <address class="address">48 Harbour Lane West, Suite 1204,<br>Toronto, Ontario, M5J 0A1</address>
    <div class="tab tab--bottom"></div>
  </section>

  <section class="card card--name">
    <div class="tab tab--corner"></div>
    <div class="brand">
      <div class="brand__mark">
        <span class="brand__square"></span>
        <span class="wordmark">brightvale</span>
      </div>
      <div class="tagline">Commerce Advancing Methods</div>
    </div>
    <div class="person">
      <div class="person__name">Martin Coles</div>
      <div class="person__title">Senior Partner</div>
    </div>
  </section>

</body>
</html>
```